Bluefern Business Services needs a new interactive and interesting website

We need an interesting, professional, modern and functional company website for Bluefern Business Services - a young IT Services company based out of Chennai, India.

Bluefern Business Services is a fully owned subsidiary of Marlow Goods, one of the world's leading direct to consumer wine merchant.

We already have a registered company logo which must feature in the website.

We conceive, design, develop, test, implement and support IT solutions across the entire Marlow Goods IT landscape. For ex : We currently run about 25 e-commerce websites for Marlow Goods on ATG and Dot Net.

We would like to see our corporate colors used in the website. (Burgundy wine and wine green - source: www.bluefernbs-site.com)

We are looking at this website to communicate a fun, friendly and professionally managed company - reaching out to career seekers, prospective customers and general public.

For reference - The company name 'Bluefern' is an inspiration from the Marlow Goods lineage.

The second image with the world map is stickered on our main entrance to the office, I am not sure where this can be used -just putting it out there..

Please note that there are only a few more days to submit designs for this contest  !

I would appreciate if you can help posting your designs in time for our review and consideration.

Thanks.

Reason: Thanks for your inputs. We have a number of designers and a lot to digest and work with in the past few days. There has been a rush of new designs in the last few days Hence we will require more time to process these and make our decision. Hence i am requesting the contest to be open for more days. Regards, Tarun

Target Market(s)

Prospective job seekers who want to know more about the company and also wish to apply for a job vacancy
People wanting to know more about the company in general and our progress
People who want to see what we offer and how we can help them too - prospective customers
Companies that are interested in our IT Captive journey and are looking for a business opportunity

Industry/Entity Type

E-Commerce

Requirements
Must have
• Log In/ Register facility acting as a Single Sign on for Intranet (Employees)

Facility to post job vacancies (with an expiry date) and enable people to apply for a role and upload their CV/Resume.

Facility to Review Job applications

Facility for website visitors to contact Bluefern business Services via an online 'Contact Us' form with a split of job seekers and business opportunities

Gallery facility to upload pictures regarding company events
Nice to have
• Less Cluttered and contemporary design
Some Wine/Vineyard inspirations will be good but not too much, the company is an IT services company

```html
<!DOCTYPE html>
<html lang="en">
<head>
<meta charset="utf-8">
<title>Bluefern Business Services</title>
<link href="https://fonts.googleapis.com/css2?family=Open+Sans:wght@400;600;700&display=swap" rel="stylesheet">
<style>
:root{
  --magenta:#a6005b;
  --magenta-dark:#8d0a4d;
  --burgundy:#8a0f4a;
  --ink:#333;
  --muted:#555;
  --line:#cfcfcf;
  --band:#efefef;
  --foot:#f3f3f3;
  --white:#fff;
}
*{box-sizing:border-box;margin:0;padding:0}
html,body{width:908px;height:1200px;overflow:hidden}
body{font-family:"Open Sans",Arial,sans-serif;color:var(--ink);background:var(--white);position:relative}
.abs{position:absolute}
.site-header{left:0;top:0;width:908px;height:190px;background:var(--magenta);overflow:hidden}
.header-curve{left:0;top:0}
.search{left:640px;top:7px;width:135px;height:18px;border:1px solid rgba(255,255,255,.55);font-size:8px;color:rgba(255,255,255,.6);padding:3px 5px}
.search svg{position:absolute;right:4px;top:3px}
.logo-mark{left:222px;top:60px;width:26px;height:26px;border-radius:50%;background:var(--white)}
.logo-name{left:258px;top:40px;font-size:38px;font-weight:700;color:var(--white);letter-spacing:-.5px}
.logo-sub{left:258px;top:88px;font-size:23px;color:var(--white)}
.nav-item{top:150px;text-align:center;color:var(--white);font-size:11px;letter-spacing:.2px}
.nav-item svg{display:block;margin:0 auto 5px}
.nav-item.active span{border-bottom:2px solid var(--white);padding-bottom:1px}
.hero{left:0;top:190px;width:908px;height:256px;background:linear-gradient(90deg,#e6ebee 0%,#d7dee3 100%)}
.hero-photo{left:440px;top:0;width:468px;height:256px;background:linear-gradient(120deg,#dfe4e8 0%,#b7bcc2 45%,#3b3c44 75%,#b49a84 100%)}
.hero-panel{left:88px;top:59px;width:326px;height:134px;background:rgba(210,218,224,.85)}
.hero-panel h2{position:absolute;left:25px;top:20px;font-size:14.5px;font-weight:600;color:var(--burgundy)}
.hero-panel p{position:absolute;left:25px;top:48px;width:290px;font-size:8.4px;line-height:11px;color:#222}
.btn{background:var(--burgundy);color:var(--white);font-size:9px;padding:0 10px;height:23px;line-height:23px;display:inline-block}
.hero-panel .btn{position:absolute;left:25px;top:89px}
.dots{top:434px;height:3px;width:53px;background:var(--white)}
.dots.on{background:var(--burgundy)}
.h-sec{font-size:14.5px;font-weight:600;color:var(--burgundy);letter-spacing:.2px}
.welcome-sub{left:130px;top:500px;font-size:10.5px;font-weight:600;color:var(--burgundy)}
.welcome-text{left:130px;top:521px;width:345px;font-size:8.4px;line-height:13px;color:#333}
.tile{width:155px;height:84px;border:1px solid var(--line)}
.tile-label{width:155px;text-align:center;font-size:9.6px;color:var(--burgundy);line-height:13px;letter-spacing:.2px}
.events{left:511px;top:473px;width:268px;height:434px;border:1px solid #c9a0b4}
.events h3{position:absolute;left:18px;top:10px;font-size:14.5px;font-weight:600;color:var(--burgundy)}
.ev-title{left:18px;font-size:9.6px;color:#222}
.ev-date{right:18px;font-size:7.6px;color:#222}
.ev-img{left:18px;width:231px;height:100px;border:1px solid var(--line)}
.ev-text{left:18px;width:236px;font-size:7.6px;line-height:10.5px;color:#333}
.ev-more{left:18px;font-size:9.5px;color:var(--burgundy)}
.clients-band{left:0;top:964px;width:908px;height:94px;background:var(--band)}
.client{top:13px;width:104px;height:68px;background:var(--white);border:1px solid #d5d5d5;display:flex;align-items:center;justify-content:center;text-align:center;font-size:11px;font-weight:600;color:var(--burgundy);line-height:13px;padding:4px}
.footer{left:0;top:1068px;width:908px;height:132px;background:var(--foot)}
.footer h4{position:absolute;left:154px;top:22px;font-size:14.5px;font-weight:600;color:var(--burgundy)}
.address{position:absolute;left:154px;top:51px;font-size:7.8px;line-height:11px;color:#333}
.social{position:absolute;top:63px;display:flex;align-items:center;font-size:7.5px;color:#333}
.circle{width:17px;height:17px;border-radius:50%}
.pill{border:1px solid #bbb;background:#fff;padding:1px 4px;font-size:7px}
.copy{position:absolute;left:569px;top:108px;font-size:8.4px;color:#555}
</style>
</head>
<body>

<header class="site-header abs">
  <svg class="header-curve abs" width="908" height="190" viewBox="0 0 908 190">
    <path d="M28 0 C40 110 230 150 430 140 C620 130 760 60 840 0 Z" fill="var(--magenta-dark)"/>
  </svg>
  <div class="search abs">Search
    <svg width="10" height="10" viewBox="0 0 10 10"><circle cx="6" cy="4" r="3" fill="none" stroke="#fff" stroke-width="1"/><line x1="4" y1="6" x2="1" y2="9" stroke="#fff" stroke-width="1.2"/></svg>
  </div>
  <div class="logo-mark abs"></div>
  <div class="logo-name abs">bluefern</div>
  <div class="logo-sub abs">Business Services</div>

  <nav>
    <div class="nav-item abs active" style="left:133px"><svg width="12" height="11" viewBox="0 0 12 11"><path d="M6 0 L12 5 H10 V11 H7 V7 H5 V11 H2 V5 H0 Z" fill="#fff"/></svg><span>HOME</span></div>
    <div class="nav-item abs" style="left:195px"><svg width="12" height="11" viewBox="0 0 12 11"><circle cx="6" cy="3" r="2.5" fill="#fff"/><path d="M1 11 C1 6 11 6 11 11 Z" fill="#fff"/></svg>ABOUT US</div>
    <div class="nav-item abs" style="left:275px"><svg width="12" height="11" viewBox="0 0 12 11"><circle cx="4" cy="7" r="3" fill="none" stroke="#fff" stroke-width="2"/><circle cx="9" cy="3" r="2" fill="none" stroke="#fff" stroke-width="1.5"/></svg>SERVICES</div>
    <div class="nav-item abs" style="left:350px"><svg width="14" height="11" viewBox="0 0 14 11"><circle cx="3" cy="3" r="2" fill="#fff"/><circle cx="7" cy="3" r="2" fill="#fff"/><circle cx="11" cy="3" r="2" fill="#fff"/><rect x="0" y="6" width="14" height="4" rx="2" fill="#fff"/></svg>CLIENTS</div>
    <div class="nav-item abs" style="left:419px"><svg width="12" height="11" viewBox="0 0 12 11"><rect x="0.5" y="0.5" width="11" height="10" fill="none" stroke="#fff"/><path d="M2 9 L6 5 L8 7 L11 2" fill="none" stroke="#fff"/></svg>CAREERS</div>
    <div class="nav-item abs" style="left:492px"><svg width="14" height="11" viewBox="0 0 14 11"><rect x="0" y="1" width="14" height="9" fill="#fff"/><path d="M0 1 L7 6 L14 1" fill="none" stroke="var(--magenta)" stroke-width="1.2"/></svg>CONTACT US</div>
    <div class="nav-item abs" style="left:653px;top:143px"><svg width="16" height="18" viewBox="0 0 16 18"><path d="M6 0 C2 0 0 3 0 5.5 C0 9 6 15 6 15 C6 15 12 9 12 5.5 C12 3 10 0 6 0 Z" fill="#fff"/><circle cx="6" cy="5.5" r="2" fill="var(--magenta)"/><path d="M10 13 L12 15 L16 11" fill="none" stroke="#fff" stroke-width="1.5"/></svg>CURRENT OPPORTUNITIES</div>
  </nav>
</header>

<section class="hero abs">
  <div class="hero-photo abs" role="img" aria-label="Photo of three business colleagues reviewing a chart on a tablet"></div>
  <div class="hero-panel abs">
    <h2>PACKAGED APPLICATIONS</h2>
    <p>The services we provide enable the businesses we support to efficiently manage key functions, including order management..</p>
    <span class="btn">Learn More &rsaquo;</span>
  </div>
</section>
<div class="dots abs on" style="left:296px"></div>
<div class="dots abs" style="left:362px"></div>
<div class="dots abs" style="left:427px"></div>
<div class="dots abs" style="left:492px"></div>

<main>
  <h2 class="h-sec abs" style="left:130px;top:468px">WELCOME TO BLUEFERN</h2>
  <div class="welcome-sub abs">Delivering IT Excellence</div>
  <p class="welcome-text abs">Welcome to Bluefern Business Services, an emerging provider of global IT consulting and software services. We are part of the Marlow Goods group, a family run business and the world's largest multi-channel home delivery wine merchant operating in the UK, USA, Australia, Germany, Hong Kong, Poland and Switzerland.</p>
  <span class="btn abs" style="left:130px;top:583px;height:24px;line-height:24px">Read More &rsaquo;</span>

  <h2 class="h-sec abs" style="left:130px;top:633px">OUR SERVICES</h2>
  <div class="tile abs" style="left:130px;top:662px;background:linear-gradient(160deg,#c9a0c0,#d8b27c 60%,#f4efe6)" role="img" aria-label="Illustration of colourful cubes in an open cardboard box"></div>
  <div class="tile-label abs" style="left:130px;top:754px">PACKAGED APPLICATIONS</div>
  <div class="tile abs" style="left:318px;top:662px;background:radial-gradient(circle at 50% 60%,#3f9a3a,#2a6fb5 55%,#fff 75%)" role="img" aria-label="Illustration of a globe connected by dotted lines"></div>
  <div class="tile-label abs" style="left:318px;top:754px">ENTERPRISE APPLICATIONS INTEGRATION</div>
  <div class="tile abs" style="left:130px;top:791px;background:linear-gradient(180deg,#f3f3f3,#d6d6d6)" role="img" aria-label="Illustration of coloured pencils in a white cup"></div>
  <div class="tile-label abs" style="left:130px;top:883px">DIGITAL COMMERCE</div>
  <div class="tile abs" style="left:318px;top:791px;background:linear-gradient(180deg,#f5f5f5,#c9ccd0 70%,#e8c34a)" role="img" aria-label="Illustration of a robot builder carrying a steel beam"></div>
  <div class="tile-label abs" style="left:318px;top:883px">APPLICATIONS DEVELOPMENT AND MAINTANANCE</div>

  <aside class="events abs">
    <h3>LATEST EVENTS</h3>
    <svg class="abs" style="right:18px;top:14px" width="16" height="12" viewBox="0 0 16 12"><path d="M6 1 L1 6 L6 11 M10 1 L15 6 L10 11" fill="none" stroke="#222" stroke-width="1.8"/></svg>
    <div class="ev-title abs" style="top:42px">Event Number1</div>
    <div class="ev-date abs" style="top:45px">Jan 1st, 2014</div>
    <div class="ev-img abs" style="top:56px;background:linear-gradient(180deg,#f6f6f6,#3a3a44)" role="img" aria-label="Group photo of the company team at the event"></div>
    <p class="ev-text abs" style="top:162px">Web application development program held at newyark city, on 01.01.14. Where all the applications got experimented with our clients.</p>
    <div class="ev-more abs" style="top:199px">More &gt;&gt;</div>
    <div class="abs" style="left:18px;top:226px;width:231px;height:1px;background:#e3e3e3"></div>
    <div class="ev-title abs" style="top:243px">Event Number1</div>
    <div class="ev-date abs" style="top:246px">Jan 1st, 2014</div>
    <div class="ev-img abs" style="top:257px;background:linear-gradient(160deg,#a9b4bf,#f2f2f2 60%,#f0d6c0)" role="img" aria-label="Illustration of a laptop surrounded by web and media symbols"></div>
    <p class="ev-text abs" style="top:363px">Web application development program held at newyark city, on 01.01.14. Where all the applications got experimented with our clients.</p>
    <div class="ev-more abs" style="top:400px">More &gt;&gt;</div>
  </aside>

  <h2 class="h-sec abs" style="left:130px;top:935px">OUR CLIENTS</h2>
  <section class="clients-band abs">
    <svg class="abs" style="left:136px;top:36px" width="12" height="22" viewBox="0 0 12 22"><path d="M11 1 L1 11 L11 21" fill="none" stroke="#aaa" stroke-width="1.5"/></svg>
    <div class="client abs" style="left:161px">Ledger Wine</div>
    <div class="client abs" style="left:281px">Ashby Cellars</div>
    <div class="client abs" style="left:402px">Marlow Goods</div>
    <div class="client abs" style="left:523px">Weekend Post Wine Club</div>
    <div class="client abs" style="left:644px">Maison Vin Direkt</div>
    <svg class="abs" style="left:760px;top:36px" width="12" height="22" viewBox="0 0 12 22"><path d="M1 1 L11 11 L1 21" fill="none" stroke="#aaa" stroke-width="1.5"/></svg>
  </section>
</main>

<footer class="footer abs">
  <h4>BLUEFERN BUSINESS SERVICES</h4>
  <p class="address">4th Floor, Orion Tech Park<br>Unit C12 Lakeview Industrial Estate<br>Velachery, Chennai, 600042<br>Tamil Nadu<br>Tel: +91 (44) 55501234<br>Email: contactus@bluefernbs-site.com</p>
  <div class="social" style="left:569px"><span class="circle" style="background:#2f7fc1"></span></div>
  <div class="social" style="left:594px"><span class="circle" style="background:#d9423b"></span></div>
  <div class="social" style="left:620px;top:65px"><span class="pill">Like</span>&nbsp;<span class="pill">54</span></div>
  <div class="social" style="left:690px;top:65px"><span class="pill">Following</span>&nbsp;<span class="pill">118</span></div>
  <p class="copy">Copyright Bluefern Business Services Private Limited.</p>
</footer>

</body>
</html>
```